Provide bookkeeping and accounting services to small and growing businesses

We need website and logo design using the name Dornaby as the logo.
The target audience are small companies and startups who need:
1) Simple bookkeeping services
2) Accounting advice that only someone with many years of senior financial experience as a CPA can provide.

The services are provided by two individuals. each of whom specialize in one of the areas.

We want the website to be clean without a lot of visual distraction but don't know how to make a boring subject interesting. We believe our potential clients, small business owners, need to find what they want quickly and easily without a lot of verbiage or distractions.

We've attached a draft of the homepage and have completed the text on most of the other pages.

Target Market(s)

small and early stage growth companies in San Diego North County

Industry/Entity Type

Accounting

Number of Pages Required

1 page

Font styles to use
Sans Serif

Colors
86cfc6
33b8a4
85cae6

Requirements
Must have
• We need a design for the website homepage that includes the name Dornaby as the logo. Must include a design for the name.
• Must have color in teal or greenish blue.
Nice to have
• White background, clean, clear, uncluttered.
• We would like to use the design in a Theme on a WordPress website. Themes Paper Lantern and Quiet Harbour are appealing to us.
Should not have
• Moving pictures

```html
<!DOCTYPE html>
<html lang="en">
<head>
<meta charset="utf-8">
<title>Dornaby – Accounting and Bookkeeping</title>
<link rel="stylesheet" href="https://fonts.googleapis.com/css2?family=Montserrat:wght@400;500;600;700&display=swap">
<style>
  :root {
    --teal: #33b8a4;
    --aqua: #86cfc6;
    --sky: #85cae6;
    --ink: #1a1a1a;
    --paper: #ffffff;
  }
  * { box-sizing: border-box; margin: 0; padding: 0; }
  html, body {
    width: 1200px; height: 1200px; overflow: hidden;
    background: var(--paper);
    font-family: "Montserrat", sans-serif;
    color: var(--ink);
  }
  .page {
    position: absolute; left: 51px; top: 197px;
    width: 955px; height: 700px;
    transform: scale(1.15); transform-origin: top left;
  }
  .page > * { position: absolute; }

  .brand { left: 0; top: 0; }
  .brand-name { font-size: 31px; font-weight: 700; color: var(--teal); line-height: 32px; letter-spacing: 0.2px; }
  .brand-tag { font-size: 9.5px; color: var(--aqua); margin-left: 3px; line-height: 10px; }

  .main-nav { right: 0; top: 10px; display: flex; gap: 19px; font-size: 14px; }
  .main-nav a { color: var(--sky); text-decoration: none; position: relative; }
  .main-nav a.is-active { color: var(--teal); font-weight: 500; }
  .main-nav a.is-active::after {
    content: ""; position: absolute; left: 0; right: 0; top: 27px;
    height: 3px; background: var(--teal); border-radius: 2px;
  }

  .hero-banner {
    left: 0; top: 60px; width: 955px; height: 88px;
    background: linear-gradient(90deg, #7d9aa6 0%, #c8b7ae 30%, #e6d9d2 45%, #b9c7d3 65%, #9fb2c8 100%);
  }

  .welcome-title { left: 0; top: 176px; font-size: 29px; font-weight: 700; color: var(--teal); letter-spacing: 0.3px; }
  .welcome-sub { left: 1px; top: 211px; font-size: 18px; color: var(--sky); }

  .intro-photo {
    left: 1px; top: 250px; width: 157px; height: 165px;
    background: linear-gradient(160deg, #b7cfe0 0%, #d9e3d6 45%, #9fbdd6 100%);
  }
  .intro-text { left: 192px; top: 277px; width: 500px; font-size: 14.6px; line-height: 20px; }

  .divider { left: 192px; top: 440px; width: 492px; height: 3px; background: var(--teal); }

  .service { width: 200px; text-align: center; top: 474px; }
  .service svg { display: block; margin: 0 auto; }
  .service-label { margin-top: 50px; font-size: 23px; font-weight: 500; line-height: 29px; letter-spacing: 0.3px; }
  .service--bookkeeping { left: 7px; }
  .service--bookkeeping .service-label { color: var(--teal); }
  .service--accounting { left: 237px; }
  .service--accounting .service-label { color: var(--sky); }
  .service--advice { left: 455px; }
  .service--advice .service-label { color: var(--sky); }

  .side-block { left: 716px; width: 239px; border-top: 3px solid var(--teal); }
  .side-block--about { top: 180px; }
  .side-block--services { top: 440px; }
  .side-title { font-size: 13.5px; font-weight: 500; color: var(--teal); margin-top: 3px; }
  .side-text { margin-top: 18px; font-size: 11px; line-height: 20px; }
  .more-link {
    display: block; text-align: right; margin-top: 12px; margin-right: 3px;
    font-size: 14px; color: var(--teal); text-decoration: underline; text-underline-offset: 3px;
  }
</style>
</head>
<body>
<main class="page">
  <header class="brand">
    <div class="brand-name">Dornaby</div>
    <div class="brand-tag">Accounting and Bookkeeping</div>
  </header>

  <nav class="main-nav">
    <a class="is-active" href="#">Home</a>
    <a href="#">About Us</a>
    <a href="#">Services</a>
    <a href="#">Experience</a>
    <a href="#">Resources</a>
    <a href="#">Contact Us</a>
  </nav>

  <div class="hero-banner" role="img" aria-label="Photo of a hand with a pencil checking figures on a ledger sheet"></div>

  <h1 class="welcome-title">WELCOME TO OUR SITE</h1>
  <p class="welcome-sub">sample text</p>

  <div class="intro-photo" role="img" aria-label="Photo of a businessman viewing financial charts"></div>
  <p class="intro-text">Dornaby offers a flexible range of accounting and bookkeeping services and support for small and growing organizations in San Diego North County. We provide bookkeeping services specializing in LedgerBooks® at your offices or remotely from ours. We also provide a broad range of accounting services or financial advice.</p>

  <div class="divider"></div>

  <section class="service service--bookkeeping">
    <svg width="124" height="124" viewBox="0 0 124 124" aria-hidden="true">
      <circle cx="62" cy="62" r="59" fill="none" stroke="var(--teal)" stroke-width="3.5"/>
      <path d="M38 50 L78 44 L108 92 L56 100 Z" fill="var(--teal)"/>
      <path d="M50 64 L80 60 M53 74 L86 70 M56 84 L92 80" stroke="#fff" stroke-width="3.5" stroke-linecap="round"/>
      <rect x="42" y="20" width="14" height="14" rx="3" fill="var(--teal)"/>
      <rect x="36" y="32" width="26" height="8" rx="3" fill="var(--teal)"/>
      <rect x="47" y="40" width="4" height="14" fill="var(--teal)"/>
    </svg>
    <div class="service-label">BOOKKEEPING</div>
  </section>

  <section class="service service--accounting">
    <svg width="124" height="124" viewBox="0 0 124 124" aria-hidden="true">
      <circle cx="62" cy="62" r="59" fill="none" stroke="var(--sky)" stroke-width="3.5"/>
      <path d="M50 36 V28 a4 4 0 0 1 4 -4 H70 a4 4 0 0 1 4 4 V36" fill="none" stroke="var(--sky)" stroke-width="5"/>
      <rect x="31" y="36" width="62" height="56" rx="6" fill="var(--sky)"/>
      <path d="M31 62 H93" stroke="#fff" stroke-width="2"/>
      <circle cx="62" cy="62" r="4" fill="#fff"/>
    </svg>
    <div class="service-label">ACCOUNTING</div>
  </section>

  <section class="service service--advice">
    <svg width="124" height="124" viewBox="0 0 124 124" aria-hidden="true">
      <circle cx="62" cy="62" r="59" fill="none" stroke="var(--sky)" stroke-width="3.5"/>
      <g fill="var(--sky)">
        <rect x="27" y="66" width="7" height="24"/>
        <rect x="38" y="58" width="7" height="32"/>
        <rect x="49" y="64" width="7" height="26"/>
        <rect x="60" y="54" width="7" height="36"/>
        <rect x="71" y="46" width="7" height="44"/>
        <rect x="82" y="38" width="7" height="52"/>
        <path d="M96 28 L78 32 L83 37 Z"/>
      </g>
      <path d="M24 66 L44 48 L56 58 L84 34" fill="none" stroke="var(--sky)" stroke-width="5" stroke-linejoin="round"/>
    </svg>
    <div class="service-label">BUSINESS<br>ADVICE</div>
  </section>

  <aside class="side-block side-block--about">
    <h2 class="side-title">About us</h2>
    <p class="side-text">Lorem ipsum dolor sit amet, consectetur<br>adipiscing elit, sed do eiusmod tempor<br>incididunt ut labore et dolore magna<br>aliqua. Ut enim ad minim veniam, quis<br>nostrud exercitation ullamco laboris nisi ut<br>aliquip ex ea commodo consequat. Duis<br>aute irure dolor in reprehenderit in<br>voluptate velit esse cillum dolore eu fugiat</p>
    <a class="more-link" href="#">more info &gt;</a>
  </aside>

  <aside class="side-block side-block--services">
    <h2 class="side-title">Our strvices</h2>
    <p class="side-text">Lorem ipsum dolor sit amet, consectetur<br>adipiscing elit, sed do eiusmod tempor<br>incididunt ut labore et dolore magna<br>aliqua. Ut enim ad minim veniam, quis<br>nostrud exercitation ullamco laboris nisi ut<br>aliquip ex ea commodo consequat. Duis<br>aute irure dolor in reprehenderit in<br>voluptate velit esse cillum dolore eu fugiat</p>
    <a class="more-link" href="#">more info &gt;</a>
  </aside>
</main>
</body>
</html>
```